Small Business Broker Business Card Design

A business card design for a small business brokerage, which is a financial service, not unlike real estate brokerage, but for small businesses such as laundromats, pizza shops, restaurants, cleaners etc. The designs should all be simple, more conservative in nature, using the colors and font of the logo. Again, think real estate Brokerage as a business context
Contact Information for Business Card
Name: Glen R. Harlow. Title: Small Business Advisor. Email: g.harlow@bayfieldcapitalworks.example. Mobile: (555) 274-3918. Office: (555) 806-2147. www.bayfieldcapitalworks.example

```html
<!DOCTYPE html>
<html lang="en">
<head>
<meta charset="utf-8">
<title>Bayfield Capital Works – Business Card</title>
<link href="https://fonts.googleapis.com/css2?family=Montserrat:wght@400;500;700&display=swap" rel="stylesheet">
<style>
  :root {
    --green: #8cc63f;
    --navy: #1d3a6e;
    --white: #ffffff;
    --ink: #2b2b2b;
    --stage: #e9ebee;
  }
  * { box-sizing: border-box; margin: 0; padding: 0; }
  html, body { width: 1200px; height: 900px; overflow: hidden; }
  body {
    background: var(--stage);
    font-family: "Montserrat", Arial, sans-serif;
    display: flex; flex-direction: column; align-items: center; justify-content: center;
    gap: 40px;
  }
  .card {
    width: 700px; height: 400px; border-radius: 22px;
    position: relative; overflow: hidden;
    box-shadow: 0 6px 20px rgba(0,0,0,.12);
  }
  .card--front {
    background: var(--green);
    display: flex; flex-direction: column; align-items: center; justify-content: center;
  }
  .brand { display: flex; align-items: center; gap: 14px; }
  .brand__mark { width: 22px; height: 22px; background: var(--navy); }
  .brand__name {
    color: var(--navy); font-weight: 700; text-transform: uppercase;
    font-size: 32px; letter-spacing: 1px;
  }
  .tagline {
    margin-top: 8px; color: var(--white); font-weight: 500;
    text-transform: uppercase; font-size: 14px; letter-spacing: 2px;
  }
  .card--back { background: var(--white); }
  .card--back .brand-block {
    position: absolute; top: 70px; right: 50px; text-align: right;
  }
  .card--back .brand { justify-content: flex-end; }
  .card--back .brand__name { font-size: 24px; }
  .card--back .brand__mark { width: 16px; height: 16px; }
  .card--back .tagline { color: var(--green); font-size: 11px; margin-top: 4px; }
  .divider-top {
    position: absolute; top: 150px; right: 50px; width: 380px; height: 1.5px; background: var(--green);
  }
  .person { position: absolute; left: 50px; top: 196px; }
  .person__name { color: var(--navy); font-weight: 700; font-size: 30px; }
  .person__title { color: var(--ink); font-size: 15px; margin-top: 2px; }
  .divider-name { width: 300px; height: 1.5px; background: var(--green); margin-top: 12px; }
  .contacts { list-style: none; position: absolute; left: 50px; top: 282px; }
  .contacts li {
    display: flex; align-items: center; gap: 10px;
    font-size: 14px; color: var(--ink); line-height: 22px;
  }
  .contacts svg { width: 14px; height: 14px; fill: var(--navy); flex: none; }
  .band { position: absolute; left: 0; right: 0; bottom: 0; height: 14px; background: var(--green); }
</style>
</head>
<body>
  <section class="card card--front" aria-label="Card front">
    <div class="brand">
      <span class="brand__mark"></span>
      <span class="brand__name">Bayfield Capital Works, Inc</span>
    </div>
    <p class="tagline">Confidently buy or sell a local business today</p>
  </section>

  <section class="card card--back" aria-label="Card back">
    <div class="brand-block">
      <div class="brand">
        <span class="brand__mark"></span>
        <span class="brand__name">Bayfield Capital Works, Inc</span>
      </div>
      <p class="tagline">Confidently buy or sell a local business today</p>
    </div>
    <div class="divider-top"></div>

    <div class="person">
      <h1 class="person__name">Glen R. Harlow</h1>
      <p class="person__title">Small Business Advisor</p>
      <div class="divider-name"></div>
    </div>

    <ul class="contacts">
      <li><svg viewBox="0 0 16 16"><path d="M1 6c0-3 3-4 7-4s7 1 7 4v1h-4V5H5v2H1zM3 8h10l1 6H2z"/></svg>(555) 806-2147</li>
      <li><svg viewBox="0 0 16 16"><path d="M3 1l3 1 1 4-2 1c1 2 2 3 4 4l1-2 4 1 1 3-2 2C7 15 1 9 1 3z"/></svg>(555) 274-3918</li>
      <li><svg viewBox="0 0 16 16"><path d="M1 3h14v10H1zM2 4l6 5 6-5v-.5H2z" fill-rule="evenodd"/></svg>g.harlow@bayfieldcapitalworks.example</li>
      <li><svg viewBox="0 0 16 16"><path d="M8 1a7 7 0 100 14A7 7 0 008 1zm0 1.5c.9 1.2 1.5 3 1.6 4.7H6.4C6.5 5.5 7.1 3.7 8 2.5zM3 8.8h2c.1 1.7.6 3.3 1.4 4.5A5.5 5.5 0 013 8.8zm3.4 0h3.2c-.1 1.7-.7 3.5-1.6 4.7-.9-1.2-1.5-3-1.6-4.7zm4.6 0h2a5.5 5.5 0 01-3.4 4.5c.8-1.2 1.3-2.8 1.4-4.5zM3 7.2a5.5 5.5 0 013.4-4.5C5.6 3.9 5.1 5.5 5 7.2zm8 0c-.1-1.7-.6-3.3-1.4-4.5A5.5 5.5 0 0113 7.2z"/></svg>www.bayfieldcapitalworks.example</li>
    </ul>

    <div class="band"></div>
  </section>
</body>
</html>
```